Holiday Rental Company Flyer Design (DL not A5)

Note from Brandloom Administration: The category sizing selected is A5, however the project requires DL sized artwork. Please refer to the DL template link below while the 'Special Requirements' are updated accordingly.

Project Brief:
We need a double sided DL flyer designed for an up market Holiday Rental Company that portrays a personalised approach to property management. These are to be used for letter box drops to homes we're specifically targeting so the design should be modern, complimentary colour palette, uncluttered & visually appealing.

Please Download the DL Template from Quillora here: http://www.quillora.com.au/ql/ns/propath/UploadResources.aspx?selectedTab=0?pfid=KMT&pf_id=KMT&xnav=easypath-upload-image#Templates

Target Market(s)

Wealthy Home Owners

Industry/Entity Type

It Company

Other font styles liked:
• Avant Garde Extra Light & Demi

Colors
33b8a4

Requirements
Must have
• DL Flyer sizes (210mm width x 99mm width, plus 3mm bleed)
• Front: Logo, Main Image & Grab
• Back: Contact Details & Brief Description of our business
• Images: Ideally the main image should be the house with the pool but alternatively a lifestyle images could also be used.
Nice to have
• A creative designer!
Should not have
• Clutter & busy designs

```html
<!DOCTYPE html>
<html lang="en">
<head>
<meta charset="utf-8">
<title>Holiday Rental Flyer – Front</title>
<link rel="stylesheet" href="https://fonts.googleapis.com/css2?family=Poppins:wght@200;300;600&display=swap">
<style>
  :root {
    --backdrop: #e9e9e7;
    --brand-teal: #33b8a4;
    --text-light: #ffffff;
    --photo-amber: #c99a45;
    --photo-warm: #8a6a48;
    --photo-stone: #6f625e;
    --photo-pool: #2a9bb5;
    --photo-pool-deep: #1b7f9c;
  }
  * { margin: 0; padding: 0; box-sizing: border-box; }
  html, body {
    width: 1200px;
    height: 870px;
    overflow: hidden;
    background: var(--backdrop);
  }
  .flyer-front {
    position: absolute;
    left: 50px;
    top: 175px;
    width: 1100px;
    height: 519px;
    overflow: hidden;
    box-shadow: 0 10px 30px rgba(0,0,0,0.18);
  }
  .hero-photo {
    position: absolute;
    inset: 0;
    background:
      linear-gradient(180deg,
        var(--photo-amber) 0%,
        #b07f3d 28%,
        var(--photo-warm) 48%,
        var(--photo-stone) 66%,
        var(--photo-pool) 80%,
        var(--photo-pool-deep) 100%);
  }
  .brand-block {
    position: absolute;
    left: 100px;
    top: 150px;
    width: 320px;
    height: 250px;
    background: var(--brand-teal);
    opacity: 0.95;
    display: flex;
    flex-direction: column;
    justify-content: center;
    padding: 0 40px;
    color: var(--text-light);
    font-family: "Poppins", sans-serif;
    font-weight: 200;
  }
  .brand-name {
    font-size: 25px;
    line-height: 1.3;
    letter-spacing: 4px;
    text-transform: uppercase;
    white-space: nowrap;
  }
  .brand-row {
    display: flex;
    align-items: center;
    justify-content: space-between;
  }
  .brand-mark {
    flex: none;
    width: 30px;
    height: 30px;
    border: 1.5px solid var(--text-light);
    border-radius: 50%;
  }
  .headline {
    position: absolute;
    right: 70px;
    bottom: 118px;
    font-family: "Poppins", sans-serif;
    font-weight: 600;
    font-size: 62px;
    line-height: 1;
    color: var(--text-light);
    letter-spacing: 1px;
    white-space: nowrap;
  }
  .tagline {
    position: absolute;
    right: 70px;
    bottom: 76px;
    font-family: "Poppins", sans-serif;
    font-weight: 300;
    font-size: 27px;
    line-height: 1.2;
    color: var(--text-light);
    letter-spacing: 1.5px;
    white-space: nowrap;
  }
</style>
</head>
<body>
  <section class="flyer-front">
    <div class="hero-photo" role="img" aria-label="Photograph of a luxury villa at dusk with lit terrace, wicker loungers, a round spa and a blue swimming pool in the foreground"></div>
    <div class="brand-block">
      <p class="brand-name">Harbourline</p>
      <div class="brand-row">
        <p class="brand-name">Retreats</p>
        <div class="brand-mark"></div>
      </div>
    </div>
    <h1 class="headline">Holiday Rental</h1>
    <p class="tagline">Management with a difference</p>
  </section>
</body>
</html>
```